Economics of an Assumption vs Obtaining a New Loan at Current Market Rate

I need to marketing flyer that has fields that calculate mortgage payments amongst other calculations. I have a rough draft that I will attach.

The idea is to provide a tool for a real estate agent to use to illustrate to a potential buyer what a payment would be if they assumed the existing loan on the house or took out a new loan at current market.

The flyer needs to be able to allow an agent to drop in their logo, photo, and contact along with the loan officers photo and contact info.

You can google open house flyer to see examples of what the overall artwork and presentation can look like.

Target Market(s)

Home Buyers

Industry/Entity Type

Real Estate

Colors
F0912C
F2A743
F7CA91
FBE8D2
FDF5EE
EE7325
F08F49
F5BC92
FAE3D3
FDF4ED

Requirements
Must have
• A way to calculate mortgage payment
Nice to have
• Photo and logo drop ins

```html
<!DOCTYPE html>
<html lang="en">
<head>
<meta charset="utf-8">
<title>Homvia – Assumption vs New Loan Flyer</title>
<link href="https://fonts.googleapis.com/css2?family=Open+Sans:ital,wght@0,400;0,600;0,700;1,400&display=swap" rel="stylesheet">
<style>
  :root{
    --orange:#EE7325;
    --orange-mid:#F0912C;
    --orange-soft:#F08F49;
    --peach:#F7CA91;
    --cream:#FDF5EE;
    --ink:#1b1b1b;
    --grey:#d9d9d9;
    --white:#ffffff;
  }
  *{box-sizing:border-box;margin:0;padding:0}
  html,body{width:856px;height:1200px;overflow:hidden;background:#fff}
  body{font-family:"Open Sans",Arial,sans-serif;color:var(--ink)}
  .flyer{position:relative;width:856px;height:1200px;background:#f8f8f8;overflow:hidden}
  .hero{position:absolute;left:0;top:0}
  .brand{position:absolute;left:110px;top:38px;display:flex;align-items:center;gap:10px}
  .brand-dot{width:34px;height:34px;border-radius:50%;background:var(--orange)}
  .brand-name{font-size:46px;font-weight:400;color:var(--orange);letter-spacing:1px;line-height:1}
  .price{position:absolute;left:157px;top:509px;font-size:31px;font-weight:700;letter-spacing:0;white-space:nowrap}
  .price-box{position:absolute;left:480px;top:511px;width:221px;height:42px;border:2px solid var(--ink);border-radius:4px;background:#fff}
  .band{position:absolute;height:43px;display:flex;align-items:center;font-weight:700;font-size:22px;letter-spacing:1.2px;
        background:linear-gradient(90deg,var(--orange-mid) 0%,var(--peach) 55%,var(--cream) 100%);border-radius:0 22px 22px 0}
  .band.current{left:12px;top:572px;width:295px;padding-left:14px}
  .band.new{left:399px;top:572px;width:432px;padding-left:14px;font-size:21px}
  .row{position:absolute;font-size:18px;font-weight:600;line-height:1}
  .colon{position:absolute;font-size:18px;font-weight:600}
  .field{position:absolute;height:23px;border:1.5px solid var(--ink);background:#fff;font-size:12.5px;font-weight:600;
         display:flex;align-items:center;padding-left:14px;white-space:nowrap}
  .field.center{justify-content:center;padding-left:0}
  .field small{font-size:7px;line-height:1;margin-left:8px;display:inline-block}
  .diff{position:absolute;left:131px;top:847px;font-size:32.5px;font-weight:700;letter-spacing:-.5px;white-space:nowrap}
  .diff-box{position:absolute;left:540px;top:852px;width:191px;height:31px;border:1.5px solid var(--ink);background:#fff;
            font-size:13.5px;display:flex;align-items:center;justify-content:center}
  .tagline{position:absolute;left:0;width:856px;top:886px;text-align:center;font-size:32px;font-weight:700;letter-spacing:-.5px}
  .footer{position:absolute;left:0;top:0}
  .pill-title{position:absolute;left:0;top:952px;width:400px;height:50px;background:#fff;border-radius:0 26px 26px 0;
              font-style:italic;font-size:20px;letter-spacing:2px;display:flex;align-items:center;padding-left:25px}
  .thumb{position:absolute;top:1017px;width:104px;height:104px;border:4px solid #fff;border-radius:12px;overflow:hidden}
  .thumb svg{display:block}
  .logo-tile{position:absolute;left:296px;top:1017px;width:104px;height:104px;background:#fff;border-radius:12px;
             display:flex;align-items:center;justify-content:center;gap:4px}
  .logo-tile .brand-dot{width:14px;height:14px}
  .logo-tile .brand-name{font-size:21px;letter-spacing:0}
  .follow{position:absolute;left:95px;top:1128px;color:#fff;font-size:17px;display:flex;align-items:center;gap:8px}
  .social{width:25px;height:25px;border:2px solid #fff;border-radius:50%}
  .cta{position:absolute;left:498px;top:955px;width:358px;height:49px;background:var(--orange-mid);border-radius:25px 0 0 25px;
       color:#fff;font-weight:700;font-size:18.5px;display:flex;align-items:center;padding-left:19px}
  .contact{position:absolute;left:508px;display:flex;align-items:center;gap:16px;font-size:18px}
  .contact b{font-weight:700}
  .icon{width:26px;height:26px}
</style>
</head>
<body>
<main class="flyer">

  <svg class="hero" width="856" height="490" viewBox="0 0 856 490">
    <defs>
      <linearGradient id="sky" x1="0" y1="0" x2="0" y2="1">
        <stop offset="0" stop-color="#5d6b8a"/>
        <stop offset=".35" stop-color="#9aa6c0"/>
        <stop offset=".5" stop-color="#b58c66"/>
        <stop offset=".8" stop-color="#a8875f"/>
        <stop offset="1" stop-color="#9d968c"/>
      </linearGradient>
      <linearGradient id="silver" x1="0" y1="0" x2="1" y2="0">
        <stop offset="0" stop-color="#9b9b9b"/>
        <stop offset=".6" stop-color="#e6e6e6"/>
        <stop offset="1" stop-color="#f8f8f8"/>
      </linearGradient>
    </defs>
    <rect role="img" aria-label="Photo of the listed home: stucco house with tile roof under a cloudy sky" x="0" y="0" width="856" height="460" fill="url(#sky)"/>
    <path d="M0 405 Q420 480 856 420 L856 490 L0 490 Z" fill="#f8f8f8"/>
    <path d="M0 425 Q400 470 856 432 L856 440 Q400 485 0 440 Z" fill="url(#silver)"/>
    <path d="M0 0 L565 0 Q470 120 290 140 Q120 150 0 95 Z" fill="var(--orange-mid)"/>
    <path d="M0 0 L530 0 Q440 118 270 134 Q110 140 0 85 Z" fill="#fff"/>
    <path d="M0 85 Q110 140 270 134 L170 142 Q70 135 0 100 Z" fill="#9b9b9b" opacity=".6"/>
  </svg>

  <div class="brand"><span class="brand-dot"></span><span class="brand-name">Homvia</span></div>

  <div class="price">PURCHASE&nbsp; PRICE :</div>
  <div class="price-box"></div>

  <div class="band current">CURRENT MORTGAGE :</div>
  <div class="band new">New Mortgage 10% Down Payment</div>

  <!-- current mortgage -->
  <div class="row" style="left:27px;top:626px">Loan ammount</div>
  <div class="row" style="left:27px;top:654px">Interest rate</div>
  <div class="row" style="left:27px;top:682px">Principal 3 interest</div>
  <div class="row" style="left:27px;top:709px">Mortgage Insurance</div>
  <div class="row" style="left:27px;top:737px">Total</div>
  <div class="row" style="left:27px;top:765px">Years</div>
  <div class="row" style="left:154px;top:765px">Months</div>
  <div class="row" style="left:27px;top:792px">Delta</div>
  <div class="colon" style="left:224px;top:622px">:</div>
  <div class="colon" style="left:224px;top:650px">:</div>
  <div class="colon" style="left:224px;top:678px">:</div>
  <div class="colon" style="left:224px;top:705px">:</div>
  <div class="colon" style="left:224px;top:733px">:</div>
  <div class="field center" style="left:242px;top:624px;width:114px">Allow Input</div>
  <div class="field center" style="left:242px;top:651px;width:114px">Allow Input</div>
  <div class="field center" style="left:242px;top:679px;width:114px">Allow Input</div>
  <div class="field center" style="left:242px;top:707px;width:114px">Allow Input</div>
  <div class="field" style="left:242px;top:735px;width:114px"></div>
  <div class="field" style="left:87px;top:762px;width:60px"></div>
  <div class="field" style="left:242px;top:762px;width:60px"></div>
  <div class="field" style="left:87px;top:790px;width:269px">Purchase price minus lean amount</div>

  <!-- new mortgage -->
  <div class="row" style="left:417px;top:626px">Loan ammount</div>
  <div class="row" style="left:417px;top:654px">Interest rate</div>
  <div class="row" style="left:417px;top:682px">Principal 3 interest</div>
  <div class="row" style="left:417px;top:709px">Mortgage Insurance</div>
  <div class="row" style="left:417px;top:737px">Total</div>
  <div class="row" style="left:417px;top:765px">Term</div>
  <div class="row" style="left:543px;top:765px">Years</div>
  <div class="row" style="left:417px;top:792px">Down payment amount</div>
  <div class="colon" style="left:614px;top:622px">:</div>
  <div class="colon" style="left:614px;top:650px">:</div>
  <div class="colon" style="left:614px;top:678px">:</div>
  <div class="colon" style="left:614px;top:705px">:</div>
  <div class="colon" style="left:614px;top:733px">:</div>
  <div class="field" style="left:632px;top:624px;width:196px">90% of purchase price</div>
  <div class="field" style="left:632px;top:651px;width:196px">Input</div>
  <div class="field" style="left:632px;top:679px;width:196px">Calc payment</div>
  <div class="field" style="left:632px;top:707px;width:196px">Input %</div>
  <div class="field" style="left:632px;top:735px;width:196px">Principal interest +<small>Mortgage<br>Insurance</small></div>
  <div class="field center" style="left:477px;top:762px;width:59px">Input</div>
  <div class="field" style="left:663px;top:790px;width:59px"></div>

  <div class="diff">PAYMENT DIFFERENCE :</div>
  <div class="diff-box">Difference Between totals</div>
  <div class="tagline">This property is “Rate Saver Approved”</div>

  <svg class="footer" width="856" height="1200" viewBox="0 0 856 1200">
    <defs>
      <linearGradient id="panel" x1="0" y1="0" x2="1" y2="0">
        <stop offset="0" stop-color="#c8c8c8"/>
        <stop offset=".25" stop-color="#f2f2f2"/>
        <stop offset="1" stop-color="#fafafa"/>
      </linearGradient>
    </defs>
    <rect x="410" y="937" width="446" height="235" fill="url(#panel)"/>
    <path d="M0 937 L417 937 Q402 1050 407 1172 L0 1172 Z" fill="var(--orange-mid)"/>
    <rect x="0" y="1172" width="856" height="28" fill="var(--orange)"/>
  </svg>

  <div class="pill-title">Picture New Mortgage</div>
  <div class="thumb" style="left:25px">
    <svg width="96" height="96" role="img" aria-label="Photo of the home exterior"><defs><linearGradient id="t1" x1="0" y1="0" x2="0" y2="1"><stop offset="0" stop-color="#7e8aa8"/><stop offset=".45" stop-color="#b48a62"/><stop offset="1" stop-color="#9c948a"/></linearGradient></defs><rect width="96" height="96" fill="url(#t1)"/></svg>
  </div>
  <div class="thumb" style="left:160px">
    <svg width="96" height="96" role="img" aria-label="Photo of the home entrance"><defs><linearGradient id="t2" x1="0" y1="0" x2="0" y2="1"><stop offset="0" stop-color="#6f7c9c"/><stop offset=".4" stop-color="#ad845d"/><stop offset="1" stop-color="#a09a90"/></linearGradient></defs><rect width="96" height="96" fill="url(#t2)"/></svg>
  </div>
  <div class="logo-tile"><span class="brand-dot"></span><span class="brand-name">Homvia</span></div>
  <div class="follow">Follow us on : <span class="social"></span><span class="social"></span></div>

  <div class="cta">For a FREE Quote Please Contact Us:</div>

  <div class="contact" style="top:1013px">
    <svg class="icon" viewBox="0 0 26 26"><circle cx="13" cy="13" r="12" fill="#fff" stroke="#333" stroke-width="1.5"/><path d="M8 7 L11 7 L12 10 L10.5 11.5 Q12 14.5 14.5 15.5 L16 14 L19 15 L19 18 Q12 19 8 11 Z" fill="#333"/></svg>
    <span>OFFICE &nbsp;: <b>0123456789</b></span>
  </div>
  <div class="contact" style="top:1049px">
    <svg class="icon" viewBox="0 0 26 26"><circle cx="13" cy="13" r="12" fill="#fff" stroke="#333" stroke-width="1.5"/><path d="M8 7 L11 7 L12 10 L10.5 11.5 Q12 14.5 14.5 15.5 L16 14 L19 15 L19 18 Q12 19 8 11 Z" fill="#333"/></svg>
    <span>MOBILE : <b>0123456789</b></span>
  </div>
  <div class="contact" style="top:1088px">
    <svg class="icon" viewBox="0 0 26 26"><circle cx="13" cy="13" r="12" fill="#fff" stroke="#333" stroke-width="1.5"/><circle cx="13" cy="13" r="7.5" fill="none" stroke="#333" stroke-width="1.5"/><path d="M5.5 13 H20.5 M13 5.5 V20.5 M13 5.5 Q8 13 13 20.5 M13 5.5 Q18 13 13 20.5" fill="none" stroke="#333" stroke-width="1.2"/></svg>
    <span>www.<b>yourwebsite</b>.com</span>
  </div>
  <div class="contact" style="top:1126px">
    <svg class="icon" viewBox="0 0 26 26"><circle cx="13" cy="13" r="12" fill="#fff" stroke="#333" stroke-width="1.5"/><path d="M7 11 L13 7 L19 11 L19 18 L7 18 Z" fill="#333"/><path d="M7 11 L13 15 L19 11" fill="none" stroke="#fff" stroke-width="1"/></svg>
    <span>youremailhere@mailbox.com</span>
  </div>

</main>
</body>
</html>
```